Business Card Design

We custom build & and install Air filtration systems for mining machines - the system filters the air going into the cabin to protect the operator/driver Examples of the machines we install our units to would be Ironhaven or Veltoro. Australian owned company Our company colors are sky blue with polished Stainless steel lettering & framing. I have a logo which I will upload but I would like the new image to be crisper.

Industry/Entity Type

Business

Contact Information for Business Card

Company name - Clearlung Pty Ltd
Dale Morrissey - Position - Sales & Product Development Contact numbers Mob 0428 359 162 Tel - 07 3581 4296
Address - 147 Quarrel Rd, Wendlebury, Brisbane 4108, Australia

Colors
0255a3

Requirements
Must have
• sky blue & polished chrome lettering

```html
<!DOCTYPE html>
<html lang="en">
<head>
<meta charset="utf-8">
<title>Clearlung Pty Ltd Business Card</title>
<link rel="stylesheet" href="https://fonts.googleapis.com/css2?family=Open+Sans:wght@400;600;700&display=swap">
<style>
  :root {
    --backdrop: #c9cbce;
    --card: #ffffff;
    --brand-blue: #0255a3;
    --sky-blue: #3aa8dc;
    --chrome: #8a9199;
    --text-dark: #3e4247;
  }
  html, body {
    margin: 0;
    width: 1200px;
    height: 902px;
    overflow: hidden;
    background: var(--backdrop);
    font-family: "Open Sans", Arial, sans-serif;
  }
  .stage { position: relative; width: 1200px; height: 902px; }
  .card {
    position: absolute;
    width: 600px;
    height: 343px;
    background: var(--card);
    box-shadow: 0 6px 18px rgba(0,0,0,0.18);
  }
  .card--front { left: 440px; top: 60px; }
  .card--back  { left: 160px; top: 470px; }

  .brand {
    display: flex;
    align-items: center;
    gap: 12px;
    color: var(--brand-blue);
    font-weight: 700;
    letter-spacing: 0.5px;
    white-space: nowrap;
  }
  .brand__mark {
    width: 24px; height: 24px;
    background: var(--sky-blue);
  }
  .card--front .brand {
    position: absolute;
    left: 50%; top: 50%;
    transform: translate(-50%, -50%);
    font-size: 40px;
  }
  .card--back .brand {
    position: absolute;
    left: 40px; top: 46px;
    font-size: 34px;
  }

  .person {
    position: absolute;
    right: 40px; top: 50px;
    text-align: right;
  }
  .person__name { color: var(--sky-blue); font-weight: 600; font-size: 19px; line-height: 26px; }
  .person__role { color: var(--chrome); font-size: 15px; line-height: 22px; }

  .website {
    position: absolute;
    right: 40px; top: 150px;
    font-size: 14px;
    letter-spacing: 3px;
    color: var(--chrome);
    white-space: nowrap;
  }
  .website strong { color: var(--sky-blue); font-weight: 600; }

  .contact {
    position: absolute;
    left: 40px; bottom: 28px;
    margin: 0; padding: 0;
    list-style: none;
    font-size: 13px;
    color: var(--text-dark);
    line-height: 22px;
    white-space: nowrap;
  }
  .contact li { display: flex; align-items: center; gap: 8px; }
  .contact svg { width: 12px; height: 12px; fill: var(--sky-blue); flex: none; }
  .contact__label { color: var(--chrome); font-weight: 600; }
</style>
</head>
<body>
<main class="stage">
  <section class="card card--front">
    <div class="brand"><span class="brand__mark"></span>Clearlung</div>
  </section>

  <section class="card card--back">
    <div class="brand"><span class="brand__mark"></span>Clearlung</div>

    <div class="person">
      <div class="person__name">Dale Morrissey</div>
      <div class="person__role">Sales &amp; Product Development</div>
    </div>

    <div class="website">www.<strong>clearlung</strong>.com.au</div>

    <ul class="contact">
      <li>
        <svg viewBox="0 0 24 24" aria-hidden="true"><path d="M6.6 10.8a15 15 0 0 0 6.6 6.6l2.2-2.2a1 1 0 0 1 1-.25 11.4 11.4 0 0 0 3.6.57 1 1 0 0 1 1 1V20a1 1 0 0 1-1 1A17 17 0 0 1 3 4a1 1 0 0 1 1-1h3.5a1 1 0 0 1 1 1c0 1.25.2 2.45.57 3.57a1 1 0 0 1-.25 1z"/></svg>
        <span><span class="contact__label">M</span> 0428 359 162 &nbsp; <span class="contact__label">T</span> 07 3581 4296</span>
      </li>
      <li>
        <svg viewBox="0 0 24 24" aria-hidden="true"><path d="M2 5h20v14H2z"/></svg>
        dale@clearlung.com.au
      </li>
      <li>
        <svg viewBox="0 0 24 24" aria-hidden="true"><path d="M12 2a7 7 0 0 0-7 7c0 5 7 13 7 13s7-8 7-13a7 7 0 0 0-7-7zm0 9.5A2.5 2.5 0 1 1 12 6.5a2.5 2.5 0 0 1 0 5z"/></svg>
        147 Quarrel Rd, Wendlebury, Brisbane 4108, Australia
      </li>
    </ul>
  </section>
</main>
</body>
</html>
```